MS Word Template for Proposals and RFP

Looking for a nice looking graphic template in MS Word. We will use this to make proposals and answer RFPs. Looking for something that will match our company brand, but give a fresh, up-to-date look and feel. There are a few pictures of a template I like. I don't necessarily like that logo - looks too "kid like" for business, but I really like how clean and organized it is. Most proposals and RFP responses are looooooonnnngggg and boring - need something that someone can look through and find what they are looking for quickly and easily.
Updates

Can't wait to see your designs!

Target Market(s)

School districts and other governmental employers

Industry/Entity Type

Business

Requirements
Must have
• Must include sample table of contents, section dividers, charts, graphs and tables that we customized based on the content. The goal is for it to look simple, clean, compelling - organized so it's easy to read, easy to find your way around - good headers, charts, flow charts, tables.... etc. Looking to have 5-10 template pages that we can use to put together and entire portfolio.
Should not have
• No "cutsie" comic sans/apple for the teacher kind of stuff - we are selling employee benefits to schools and other governmental entities. Should be more serious and conservative but also look compelling and draw in the reader.

```html
<!DOCTYPE html>
<html lang="en">
<head>
<meta charset="UTF-8">
<title>Keystone Benefit Group – Corporate Profile</title>
<link rel="stylesheet" href="https://fonts.googleapis.com/css2?family=Roboto+Slab:wght@300&display=swap">
<style>
  :root {
    --brand-blue: #5b7fc4;
    --title-blue: #5a78c0;
    --title-grey: #8a8d93;
    --name-grey: #7f8fb8;
    --paper: #ffffff;
    --sky-light: #eef2f9;
    --sky-mid: #b9c8e8;
    --sky-deep: #8ea4d6;
    --sky-lilac: #c7bfe0;
  }
  * { margin: 0; padding: 0; box-sizing: border-box; }
  html, body { width: 900px; height: 1200px; overflow: hidden; background: var(--paper); }
  .cover {
    position: relative;
    width: 900px;
    height: 1200px;
    background: var(--paper);
    font-family: "Roboto Slab", Georgia, serif;
  }
  .cover-photo {
    position: absolute;
    left: 0; top: 0;
    width: 900px; height: 742px;
    background:
      radial-gradient(ellipse at 20% 25%, rgba(255,255,255,0.8), rgba(255,255,255,0) 45%),
      radial-gradient(ellipse at 35% 78%, var(--sky-lilac), rgba(199,191,224,0) 40%),
      linear-gradient(160deg, var(--sky-light) 0%, var(--sky-mid) 45%, var(--sky-deep) 75%, var(--sky-light) 100%);
  }
  .cover-title {
    position: absolute;
    left: 0; right: 0;
    top: 828px;
    text-align: center;
    font-weight: 300;
    font-size: 40px;
    letter-spacing: -0.5px;
    color: var(--title-grey);
  }
  .cover-title .accent { color: var(--title-blue); }
  .company-name {
    position: absolute;
    left: 0; right: 0;
    top: 990px;
    display: flex;
    justify-content: center;
    align-items: center;
    gap: 22px;
  }
  .company-name .mark {
    width: 26px; height: 26px;
    background: var(--name-grey);
  }
  .company-name .wordmark {
    font-weight: 300;
    font-size: 48px;
    letter-spacing: 2px;
    text-transform: uppercase;
    color: var(--name-grey);
  }
  .footer-band {
    position: absolute;
    left: 0; bottom: 0;
    width: 900px; height: 57px;
    background: var(--brand-blue);
  }
</style>
</head>
<body>
  <main class="cover">
    <div class="cover-photo" role="img" aria-label="Photograph of two business people shaking hands against a soft blue sky"></div>
    <h1 class="cover-title"><span class="accent">Company</span> Corporate Profile</h1>
    <div class="company-name">
      <span class="mark"></span>
      <span class="wordmark">Keystone Benefit Group</span>
    </div>
    <div class="footer-band"></div>
  </main>
</body>
</html>
```